Freelance Translator in Need of a Business Card

I am a freelance Japanese to English translator. I work in the video game localization industry and do literary translation in my spare time. I would like to have both the English word 'Translator' and the Japanese '翻訳者' in the job title. The final design should evoke trust, openness, and reliability.

Target Market(s)

Video game localization companies
Japanese comic book artists

Industry/Entity Type

Business

Contact Information for Business Card

Daniel Forsvik, Translator
dan.forsvik@quellmail.net
torvenwords.com
social: @torven_wd

Colors

Designer to choose colors to be used in the design.

```html
<!DOCTYPE html>
<html lang="en">
<head>
<meta charset="utf-8">
<title>Daniel Forsvik – Business Card</title>
<link rel="stylesheet" href="https://fonts.googleapis.com/css2?family=Tinos:ital,wght@0,400;1,700&family=Lato:wght@400&family=Noto+Sans+JP:wght@400&display=swap">
<style>
  :root {
    --backdrop: #3b3b3b;
    --card: #0b0b0b;
    --ink: #ffffff;
    --rule: #e6e6e6;
  }
  * { margin: 0; padding: 0; box-sizing: border-box; }
  html, body {
    width: 1200px;
    height: 750px;
    overflow: hidden;
    background: var(--backdrop);
  }
  .canvas {
    position: relative;
    width: 1200px;
    height: 750px;
  }
  .card {
    position: absolute;
    left: 366px;
    width: 467px;
    height: 267px;
    background: var(--card);
    color: var(--ink);
  }
  .card--front { top: 93px; }
  .card--back { top: 406px; }

  .front-frame {
    position: absolute;
    inset: 16px;
    border: 1px solid var(--rule);
    display: flex;
    align-items: center;
    justify-content: center;
  }
  .front-name {
    font-family: "Tinos", "Times New Roman", serif;
    font-weight: 400;
    font-size: 25px;
    letter-spacing: 0.5px;
    margin-top: -8px;
  }

  .back-name {
    position: absolute;
    top: 93px;
    width: 100%;
    text-align: center;
    font-family: "Tinos", "Times New Roman", serif;
    font-weight: 400;
    font-size: 21px;
    letter-spacing: 0.4px;
  }
  .back-title {
    position: absolute;
    top: 119px;
    width: 100%;
    text-align: center;
    font-family: "Lato", "Noto Sans JP", sans-serif;
    font-size: 12px;
  }
  .back-title .title-ja {
    font-family: "Noto Sans JP", sans-serif;
    margin-left: 10px;
  }
  .contact-list {
    position: absolute;
    top: 150px;
    width: 100%;
    list-style: none;
    text-align: center;
    font-family: "Lato", sans-serif;
    font-size: 12px;
    line-height: 16px;
  }
  .contact-label {
    font-family: "Tinos", "Times New Roman", serif;
    font-style: italic;
    font-weight: 700;
    margin-right: 3px;
  }
  .back-rule {
    position: absolute;
    left: 0;
    top: 240px;
  }
</style>
</head>
<body>
<main class="canvas">
  <section class="card card--front" aria-label="Card front">
    <div class="front-frame">
      <h1 class="front-name">DANIEL FORSVIK</h1>
    </div>
  </section>

  <section class="card card--back" aria-label="Card back">
    <h2 class="back-name">DANIEL FORSVIK</h2>
    <p class="back-title">Translator<span class="title-ja" lang="ja">翻訳者</span></p>
    <ul class="contact-list">
      <li><span class="contact-label">email:</span>dan.forsvik@quellmail.net</li>
      <li><span class="contact-label">web:</span>torvenwords.com</li>
      <li><span class="contact-label">social:</span>@torven_wd</li>
    </ul>
    <svg class="back-rule" width="467" height="12" viewBox="0 0 467 12" aria-hidden="true">
      <line x1="0" y1="6" x2="191" y2="6" stroke="var(--rule)" stroke-width="1"/>
      <line x1="275" y1="6" x2="467" y2="6" stroke="var(--rule)" stroke-width="1"/>
      <g fill="var(--ink)">
        <circle cx="199" cy="6" r="1.3"/>
        <circle cx="215" cy="6" r="1.3"/>
        <circle cx="231" cy="6" r="1.3"/>
        <circle cx="247" cy="6" r="1.3"/>
        <circle cx="263" cy="6" r="1.3"/>
      </g>
    </svg>
  </section>
</main>
</body>
</html>
```